Stationery Design Project

We need a stationery design for our Norwegian trucking company. We have existed for about 15 years and our 12 drivers uses relatively new vehicles to transport goods around in northern Norway. Long distance routes with fresh fish og food transport is our main operations.

We have already made alogo that's printed on our trucks. The logo and a picture of our trucks is attached. I think the logo i crappy, but since its already in use, changing it is not an option in this round. Still using a better colour scheme in the overall stationery and more interesting fonts is possible (altso in the logo).

Company details:
Name: Kjelvraket AS
Organisation nr 873 615 309
Post adress: 8642 Raudvik

I like minimalism and simplicity. I am avalibly for questions in normal GMT working hours either here or on mail: ivar@fjordlast.no

Reason: Hi. Im extending the deadline because I needed some time to find a vector file of our logo. Sorry for the inconvenience

Hi, and thanks for all your interest in the project. Some updates:

-          I have decided to commit to using one of the designs. Some designer will get the payment.

-          I have extended the deadline with 24 hours since I needed some time to find our firms vector logo (a slow Swedish man was holding me up)

-          We will not choose a design before the deadline. No need to rush.

-          We have received a lot of great design and think there is a need to specified the product we want to make:

o   Business Card for all our employers. I just need the design and will duplicate with the correct numbers and name myself. The information on should be: Logo, employer’s name, Phone number, email, website, Postal number and address. Use this as a template: logo, Leif Brattvoll, 47382066, Leif@fjordlast.no,, fjordlast.no, 8642 Raudvik. The order and placement of the information is your creative decision.

o   Stickers to put on the goods we travel. On the sticker the should be the following information: Logo, phone number, Tekst and link: Fraktæ av Kjelvraket. Ke du syns? Fjordlast.no/tilbakemelding (this means: Handled by Kjelvraket. What do you think Fjordlast.no/feedback -à the link will be a feedback form). The placement the information and size is your creative decision with some stings: we have been thinking of using Drukko for printing and see that a size about 6x6 cm, 8x5 or something like that. (with 3000 copies our budget is 200 punds). Any suggestions of other suppliers are welcome. Drukko price calculator http://www.drukkolabelhouse.co.uk/digital-litho-printing/printing-labels-tags/stickers/

o   Letterhead with logo, address, phone number and organizational number.

o   Envelopes with logo,address, phone number and organizational number.

Have a nice day.

 

 

• Using the blue colour in the logo and using a similar graphic approch.

```html
<!DOCTYPE html>
<html lang="no">
<head>
<meta charset="utf-8">
<title>Kjelvraket AS – visittkort</title>
<link href="https://fonts.googleapis.com/css2?family=Open+Sans:wght@400;600;700;800&display=swap" rel="stylesheet">
<style>
  :root {
    --navy: #0a4da0;
    --sky: #0a73b9;
    --ink: #222831;
    --paper: #ffffff;
    --stage-light: #b9bcc0;
    --stage-dark: #5e6267;
    --line-soft: #5fa8de;
  }
  * { box-sizing: border-box; margin: 0; padding: 0; }
  html, body { width: 1200px; height: 751px; overflow: hidden; }
  body {
    position: relative;
    font-family: "Open Sans", Arial, sans-serif;
    background: linear-gradient(135deg, var(--stage-light) 0%, var(--stage-dark) 50%, var(--stage-light) 100%);
  }
  .card {
    position: absolute;
    width: 525px;
    height: 300px;
    border-radius: 26px;
    overflow: hidden;
  }
  .card--front { left: 50px; top: 50px; background: var(--paper); border: 1px solid #2a2a2a; }
  .card--white { left: 619px; top: 50px; background: var(--paper); border: 1px solid #2a2a2a; }
  .card--navy  { left: 50px; top: 388px; background: var(--navy); }
  .card--sky   { left: 619px; top: 388px; background: var(--sky); }

  .card__wave { position: absolute; inset: 0; width: 100%; height: 100%; }

  .card__name {
    position: absolute; right: 36px; top: 24px;
    color: var(--paper); font-weight: 700; font-size: 19px;
  }

  .brand {
    position: absolute; left: 0; right: 0;
    display: flex; align-items: center; justify-content: center; gap: 14px;
    font-weight: 800; font-size: 50px; letter-spacing: -0.5px;
    color: var(--navy);
  }
  .brand__dot {
    width: 22px; height: 22px; border-radius: 50%; background: currentColor;
  }
  .card--front .brand { top: 118px; justify-content: flex-start; padding-left: 96px; }
  .card--white .brand { top: 118px; }
  .card--navy .brand, .card--sky .brand { top: 118px; color: var(--paper); }

  .card__web {
    position: absolute; left: 0; right: 0; top: 248px;
    text-align: center; font-size: 17px; letter-spacing: 3.5px;
    color: var(--ink);
  }
  .card--navy .card__web, .card--sky .card__web { color: var(--paper); }

  .contact { position: absolute; font-size: 15px; color: var(--ink); line-height: 24px; }
  .contact__org { left: 39px; top: 210px; }
  .contact__org span { color: var(--sky); }
  .contact__left { left: 39px; top: 234px; }
  .contact__right { left: 208px; top: 236px; }
  .contact__divider {
    position: absolute; left: 191px; top: 242px; width: 1px; height: 36px; background: #9aa3ad;
  }
  .contact__row { display: flex; align-items: center; gap: 6px; }
  .contact__row svg { width: 12px; height: 12px; fill: var(--navy); flex: none; }
</style>
</head>
<body>

<section class="card card--front">
  <svg class="card__wave" viewBox="0 0 525 300" preserveAspectRatio="none" aria-hidden="true">
    <path d="M0,0 H525 V152 C420,70 230,18 0,48 Z" fill="var(--navy)"/>
    <path d="M0,52 C200,26 390,70 525,158" fill="none" stroke="var(--paper)" stroke-width="4"/>
    <path d="M0,60 C220,34 400,82 525,166" fill="none" stroke="var(--line-soft)" stroke-width="2"/>
  </svg>
  <p class="card__name">Leif Brattvoll</p>
  <div class="brand"><span class="brand__dot"></span>Kjelvraket</div>

  <p class="contact contact__org"><span>Org nr</span> 873 615 309</p>
  <div class="contact contact__left">
    <p class="contact__row"><svg viewBox="0 0 12 12"><path d="M1 5 L6 1 L11 5 V11 H1 Z"/></svg>8642 Raudvik</p>
    <p class="contact__row"><svg viewBox="0 0 12 12"><path d="M2 1 H5 L6 4 L4 5 C5 7 6 8 8 8 L9 6 L12 7 V10 C12 11 11 12 10 12 C5 12 0 7 0 3 C0 2 1 1 2 1 Z"/></svg>47382066</p>
  </div>
  <span class="contact__divider"></span>
  <div class="contact contact__right">
    <p class="contact__row"><svg viewBox="0 0 12 12"><path d="M0 3 H12 V10 H0 Z M0 3 L6 7 L12 3"/></svg>Leif@fjordlast.no</p>
    <p class="contact__row"><svg viewBox="0 0 12 12"><circle cx="6" cy="6" r="5.5"/></svg>www.fjordlast.no</p>
  </div>
</section>

<section class="card card--white">
  <div class="brand"><span class="brand__dot"></span>Kjelvraket</div>
  <p class="card__web">www.fjordlast.no</p>
</section>

<section class="card card--navy">
  <div class="brand"><span class="brand__dot"></span>Kjelvraket</div>
  <p class="card__web">www.fjordlast.no</p>
</section>

<section class="card card--sky">
  <div class="brand"><span class="brand__dot"></span>Kjelvraket</div>
  <p class="card__web">www.fjordlast.no</p>
</section>

</body>
</html>
```